Tampa Bay fishing guide needs stunning website.

I currently have a site - www.reelcoveguide.net which I personally put together using the Pagely platform and I am looking for a redesign on a different platform (Sitecraft?) that will allow me to easily create landing pages in the future. Would like to have a block for visitors to opt in to newsletter. Need social media links on all pages.

I would like to let my visitors know that I am able to handle their fishing charter needs here in the Tampa Bay area, if I'm not available for the dates they are looking to go I can refer them to a reputable captain in the area.

Target Market(s)

United States

Industry/Entity Type

Tourism

Coding

Coded - Design and coding required

Number of Pages Required

5+ page

Font styles to use
Sans Serif

Colors
0355a3
3176b5
85abd2
fbf289

Requirements
Must have
• Mobile Responsive, Ability to insert Vantor Metrics, Chatterbox pixels, ability to add custom landing pages in future
Nice to have
• Clean, easy navigation

```html
<!DOCTYPE html>
<html lang="en">
<head>
<meta charset="utf-8">
<title>Capt. Wade Halvorsen – Tampa Bay Fishing Charters</title>
<link href="https://fonts.googleapis.com/css2?family=Raleway:wght@400;600;700&family=Open+Sans:ital,wght@0,400;0,600;0,700;1,400&display=swap" rel="stylesheet">
<style>
:root{
  --navy:#0355a3;
  --blue:#3176b5;
  --sky:#85abd2;
  --lemon:#fbf289;
  --gold:#ecd94f;
  --ink:#333;
  --muted:#777;
  --line:#e2e2e2;
  --dark:#1c1c1c;
  --sea:#123244;
}
*{box-sizing:border-box;margin:0;padding:0}
html,body{width:1200px;height:2384px;overflow:hidden}
body{background:linear-gradient(160deg,#1d4658 0%,var(--sea) 50%,#0c2431 100%);font-family:"Open Sans",sans-serif;color:var(--ink)}
.page{position:absolute;left:98px;top:0;width:1004px;height:2384px;background:#fff}
h2,h3,h4,.nav,.btn{font-family:"Raleway",sans-serif}

/* header */
.site-header{height:129px;position:relative}
.call{position:absolute;left:22px;top:54px;display:flex;align-items:center;gap:10px;font-size:14px;color:var(--blue);font-family:"Raleway",sans-serif;font-weight:600}
.call b{color:var(--navy)}
.brand{position:absolute;left:0;right:0;top:44px;text-align:center;font-family:"Raleway",sans-serif;font-weight:700;font-size:30px;color:var(--navy)}
.search{position:absolute;left:730px;top:52px;width:253px;height:27px;border:1px solid #ddd;font-size:10px;color:#999;padding:6px 10px;display:flex;justify-content:space-between;align-items:center}

.nav{display:flex;height:49px;background:var(--blue);font-size:11px;font-weight:700;color:#fff;letter-spacing:.3px}
.nav a{display:flex;align-items:center;justify-content:center;flex:1;border-right:1px solid rgba(255,255,255,.12);text-decoration:none;color:inherit}
.nav .home{flex:0 0 110px;background:var(--navy)}
.nav .gift{flex:0 0 160px;background:linear-gradient(var(--lemon),var(--gold));color:var(--ink);border:none}

/* hero */
.hero{position:relative;height:436px;background:linear-gradient(180deg,#7fb3c9 0%,#3f8fa6 35%,#2a7f8f 70%,#1f6a78 100%)}
.hero-caption{position:absolute;top:180px;left:0;right:0;text-align:center;color:#fff}
.hero-caption h2{font-size:27px;color:var(--lemon);font-weight:700;letter-spacing:.3px}
.hero-caption p{margin:10px auto 0;width:520px;font-size:13.5px;line-height:1.7;font-weight:600}
.dots{position:absolute;top:298px;left:0;right:0;display:flex;justify-content:center;gap:14px}
.dots span{width:12px;height:12px;border-radius:50%;border:2px solid #fff}
.dots span:first-child{background:var(--lemon);border-color:var(--lemon)}

/* intro */
.intro{height:416px;background:var(--blue);color:#fff;position:relative}
.intro h2{position:absolute;top:38px;left:0;right:0;text-align:center;font-size:24px;line-height:1.6;font-weight:600}
.intro-photo{position:absolute;left:19px;top:130px;width:394px;height:228px;border:4px solid #fff;background:linear-gradient(135deg,#dfe4e6 0%,#9bb5a8 40%,#2f8a6a 100%)}
.intro-text{position:absolute;left:466px;top:126px;width:510px;font-size:11.3px;line-height:2}
.intro-text p+p{margin-top:10px}
.btn{display:inline-flex;align-items:center;justify-content:center;background:linear-gradient(var(--lemon),var(--gold));color:var(--ink);font-size:10.5px;font-weight:700;border-radius:3px;box-shadow:0 2px 2px rgba(0,0,0,.2)}
.intro .btn{position:absolute;left:466px;top:314px;width:140px;height:42px}

/* rates */
.rates{height:501px;position:relative;text-align:center}
.section-title{font-size:22px;font-weight:700;color:var(--blue)}
.rates .section-title{padding-top:40px}
.rates .lede{font-style:italic;font-size:11.3px;color:#666;margin-top:6px}
.cards{position:absolute;top:123px;left:19px;display:flex;gap:27px}
.card{width:304px;height:334px;border:1px solid var(--line);border-radius:4px;overflow:hidden;position:relative}
.card-photo{height:167px}
.p1{background:linear-gradient(180deg,#6f8f68 0%,#8ea77a 45%,#c9ccc3 70%,#8a9aa3 100%)}
.p2{background:linear-gradient(180deg,#7a8d94 0%,#b6bcbd 45%,#c9c5bb 100%)}
.p3{background:linear-gradient(180deg,#5b7a52 0%,#4376b4 45%,#2c62a6 100%)}
.ribbon{position:absolute;left:0;top:0;width:78px;height:78px;background:var(--lemon);clip-path:polygon(0 0,100% 0,0 100%)}
.ribbon span{position:absolute;left:0;top:22px;width:62px;transform:rotate(-45deg);font-family:"Raleway",sans-serif;font-size:9.5px;font-weight:700;color:var(--ink);text-align:center}
.card h4{margin-top:20px;font-size:12px;font-weight:700;color:#222}
.price{font-family:"Raleway",sans-serif;color:var(--blue);font-weight:700;font-size:19px;margin-top:10px}
.group{font-size:11px;font-weight:600;margin-top:6px;color:#222}
.group b{color:var(--blue);font-size:17px;font-family:"Raleway",sans-serif}
.card .btn{margin-top:16px;width:228px;height:34px}

/* features */
.features{height:286px;background:var(--blue);position:relative;color:#fff}
.features .section-title{color:#fff;text-align:center;padding-top:44px}
.feature{position:absolute;top:100px;display:flex;gap:32px}
.feature.left{left:19px}
.feature.right{left:527px}
.disc{width:135px;height:135px;border-radius:50%;flex:none}
.d1{background:linear-gradient(160deg,#5d8a54,#c9a47f 55%,#a88d6e)}
.d2{background:linear-gradient(180deg,#e6a15c 0%,#c9707a 40%,#3a4f7a 75%,#1d2f52 100%)}
.feature h4{font-size:12px;font-weight:700;margin-top:14px}
.feature p{font-size:11px;line-height:1.95;margin-top:10px;width:296px}
.more{color:var(--lemon);font-size:10.5px;font-weight:600}

/* availability */
.avail{height:334px;position:relative}
.avail h3{position:absolute;left:19px;top:40px;font-size:14.5px;font-weight:700;color:var(--navy)}
.calendar{position:absolute;left:19px;top:78px;width:270px;border:1px solid var(--line);font-size:8.5px}
.cal-head{display:flex;justify-content:space-between;align-items:center;height:32px;border-bottom:1px solid var(--line);color:var(--navy);font-family:"Raleway",sans-serif;font-weight:700;font-size:11px}
.cal-head i{width:16px;height:32px;background:var(--navy);display:flex;align-items:center;justify-content:center}
.cal-grid{display:grid;grid-template-columns:repeat(7,1fr);gap:4px;padding:8px 10px 12px}
.cal-grid .dow{font-weight:700;text-align:center;color:#333;height:16px}
.cal-grid span{height:22px;border:1px solid #e6e6e6;display:flex;align-items:center;justify-content:center;color:#555}
.cal-grid .hl{background:var(--lemon);border-color:var(--lemon)}
.cal-grid .sel{border:2px solid var(--gold);font-weight:700}
.cal-grid .bold{background:var(--lemon);font-weight:700}
.cal-grid .off{color:#bbb}
.notices{position:absolute;left:309px;top:76px;width:318px}
.tab{display:inline-block;border:1px solid var(--line);border-bottom:none;padding:10px 14px;font-family:"Raleway",sans-serif;font-size:10px;font-weight:700;color:var(--navy);background:#fff;position:relative;top:1px}
.notice-list{border:1px solid var(--line);padding:0 18px}
.notice{padding:18px 0 14px;font-size:10.7px;line-height:1.8}
.notice+.notice{border-top:1px solid var(--line)}
.notice a{color:var(--blue);text-decoration:none}
.notice p{color:#777}
.notice u{color:var(--blue)}
.newsletter{position:absolute;left:672px;top:42px;width:312px;height:268px;background:#f5f5f5}
.newsletter h4{background:var(--navy);color:#fff;text-align:center;height:40px;line-height:40px;font-size:14px;font-weight:600}
.newsletter form{padding:14px 18px}
.newsletter .field{height:36px;background:#fff;border:1px solid #e8e8e8;border-radius:3px;margin-bottom:7px;font-size:9.5px;color:#999;text-align:center;line-height:36px}
.newsletter .btn{width:100%;height:36px;font-size:11px}

/* footer */
.site-footer{height:189px;background:var(--dark);color:#bbb;position:relative;font-size:11px}
.col{position:absolute;top:30px}
.col h5{font-family:"Raleway",sans-serif;color:#fff;font-size:11.5px;font-weight:700;margin-bottom:16px}
.col li{list-style:none;line-height:2}
.c1{left:19px}.c2{left:236px}.c3{left:463px;width:290px}.c4{left:818px;width:170px}
.contact li{display:flex;gap:8px;align-items:center}
.news-nav{position:absolute;right:0;top:0;color:#888;font-size:12px}
.news-item{background:#fff;display:flex;gap:10px;padding:5px;width:290px}
.news-photo{width:80px;height:62px;background:linear-gradient(160deg,#9bb9c7,#3c6e86 60%,#d0b68f)}
.news-item p{font-size:10.3px;line-height:1.6;color:#888}
.news-item b{color:var(--blue);font-weight:400}
.news-item em{color:var(--blue);font-style:normal}
.c4 p{font-style:italic;line-height:1.8;color:#999}
.social{display:flex;gap:9px;margin-top:12px}
.social span{width:26px;height:26px;border:1.5px solid #ddd;border-radius:50%}
.copyright{height:44px;background:var(--blue);color:#fff;text-align:center;line-height:44px;font-size:10px;font-family:"Raleway",sans-serif;letter-spacing:.3px}
</style>
</head>
<body>
<div class="page">

  <header class="site-header">
    <div class="call">
      <svg width="20" height="20" viewBox="0 0 20 20"><rect width="20" height="20" rx="3" fill="#3176b5"/><path d="M6 4.5l2 .3 1 2.8-1.3 1a7 7 0 0 0 3.7 3.7l1-1.3 2.8 1 .3 2A1.6 1.6 0 0 1 13.9 15 9 9 0 0 1 5 6.1a1.6 1.6 0 0 1 1-1.6z" fill="#fff"/></svg>
      <span>Call Us : <b>813-555-0182</b></span>
    </div>
    <div class="brand">Capt. Wade Halvorsen</div>
    <div class="search"><span>SEARCH...</span>
      <svg width="10" height="10" viewBox="0 0 10 10"><circle cx="4" cy="4" r="3" fill="none" stroke="#aaa" stroke-width="1.3"/><path d="M6.3 6.3L9 9" stroke="#aaa" stroke-width="1.3"/></svg>
    </div>
  </header>

  <nav class="nav">
    <a class="home" href="#">HOME</a>
    <a href="#">ABOUT US</a>
    <a href="#">PICK UP LOCATIONS</a>
    <a href="#">RATES</a>
    <a href="#">CONTACT US</a>
    <a class="gift" href="#">GIFT CARD</a>
  </nav>

  <section class="hero" role="img" aria-label="Anglers on a boat fighting a leaping tarpon on open bay water">
    <div class="hero-caption">
      <h2>FISHING GUIDE &amp; FISHING CHARTERS</h2>
      <p>Capt. Wade Halvorsen, with over 20 years' experience, Native fishing charter tampa charter captain offering full and half day fishing....</p>
    </div>
    <div class="dots"><span></span><span></span><span></span></div>
  </section>

  <section class="intro">
    <h2>TAMPA BAY, FISHING GUIDE , TAMPA BAY<br>FISHING CHARTERS</h2>
    <div class="intro-photo" role="img" aria-label="Anglers on deck holding up a large tarpon beside the boat"></div>
    <div class="intro-text">
      <p>Capt. Wade Halvorsen, with over 20 years' experience, Native fishing charter tampa charter captain offering full and half day fishing charters on the waters of Tampa Bay.If you're looking for a great fishing charter tampa don't hesitate to contact Capt. Wade or you can simply book your trip online here.Come enjoy a wonderful day fishing charters</p>
      <p>Tampa for Tarpon, Snook, Redfish, Trout, Sharks, Cobia,Spanish mackerel as well as others aboard Capt. Wade Halvorsen Sport fishing Charters boat. Capt. Wade will work hard to ensure that you and your guests have a memorable day enjoying the wonderful gamefish that Tampa Bay has to offer.</p>
    </div>
    <a class="btn" href="#">READ MORE INFO</a>
  </section>

  <section class="rates">
    <h2 class="section-title">RATES</h2>
    <p class="lede">Recommend you bring sunglasses, hat, and sunscreen.  Capt. Wade will clean and bag all fish that you wish to take home..</p>
    <div class="cards">
      <article class="card">
        <div class="card-photo p1" role="img" aria-label="Center console fishing boat by a mangrove shoreline"></div>
        <div class="ribbon"><span>HALF DAY</span></div>
        <h4>(4 HOUR) CHARTER 1-3 PEOPLE</h4>
        <div class="price">$399</div>
        <div class="group">4 PEOPLE &nbsp;&gt;&gt; <b>$499</b></div>
        <a class="btn" href="#">CLICK TO BOOK NOW!</a>
      </article>
      <article class="card">
        <div class="card-photo p2" role="img" aria-label="Two anglers on a boat holding a large tarpon"></div>
        <div class="ribbon"><span>3/4 DAY</span></div>
        <h4>(6 HOUR) CHARTER 1-3 PEOPLE</h4>
        <div class="price">$499</div>
        <div class="group">4 PEOPLE &nbsp;&gt;&gt; <b>$599</b></div>
        <a class="btn" href="#">CLICK TO BOOK NOW!</a>
      </article>
      <article class="card">
        <div class="card-photo p3" role="img" aria-label="Angler in a blue shirt holding a snook"></div>
        <div class="ribbon"><span>FULL DAY</span></div>
        <h4>(8 HOURS) CHARTER 1-3 PEOPLE</h4>
        <div class="price">$599</div>
        <div class="group">4 PEOPLE &nbsp;&gt;&gt; <b>$699</b></div>
        <a class="btn" href="#">CLICK TO BOOK NOW!</a>
      </article>
    </div>
  </section>

  <section class="features">
    <h2 class="section-title">FEATURES</h2>
    <div class="feature left">
      <div class="disc d1" role="img" aria-label="Two anglers holding a snook"></div>
      <div>
        <h4>FULL &amp; HALF DAY CHARTERS</h4>
        <p>Offering Tampa Bay, FL fishing charters on the beautiful waters of Tampa Bay. Fish with Capt. Wade Halvorsen, Tampa Bay, FL fishing guide for over 20 years</p>
        <span class="more">Learn More ⟶</span>
      </div>
    </div>
    <div class="feature right">
      <div class="disc d2" role="img" aria-label="Wooden pier reaching into the bay at sunset"></div>
      <div>
        <h4>MULTIPLE PICKUP POINTS</h4>
        <p>Whether you're looking for a fishing charter/guide in Tampa, St. Pete, Clearwater or Bradenton, Capt. Wade can pick you up nearby. Click here for maps...</p>
        <span class="more">Learn More ⟶</span>
      </div>
    </div>
  </section>

  <section class="avail">
    <h3>SELECT YOUR AVAILABLE DATES FOR TAMPA BAY AREA</h3>
    <div class="calendar">
      <div class="cal-head">
        <i><svg width="7" height="10" viewBox="0 0 7 10"><path d="M6 1L2 5l4 4" stroke="#fff" stroke-width="2" fill="none"/></svg></i>
        SEPTEMBER
        <i><svg width="7" height="10" viewBox="0 0 7 10"><path d="M1 1l4 4-4 4" stroke="#fff" stroke-width="2" fill="none"/></svg></i>
      </div>
      <div class="cal-grid">
        <div class="dow">Mon</div><div class="dow">Tue</div><div class="dow">Wed</div><div class="dow">Thu</div><div class="dow">Fri</div><div class="dow">Sat</div><div class="dow">Sun</div>
        <span>1</span><span>2</span><span>3</span><span class="hl">4</span><span>5</span><span>6</span><span>7</span>
        <span>8</span><span class="hl">9</span><span>10</span><span>11</span><span>12</span><span class="bold">13</span><span>14</span>
        <span>15</span><span>16</span><span>17</span><span>18</span><span>19</span><span>20</span><span>21</span>
        <span>22</span><span>23</span><span>24</span><span>25</span><span>26</span><span>27</span><span>28</span>
        <span>29</span><span class="sel">30</span><span>31</span><span class="off">1</span><span class="off">2</span><span class="off">3</span><span class="off">4</span>
      </div>
    </div>
    <div class="notices">
      <div class="tab">I'M NOT &nbsp;AVAILABLE</div>
      <div class="notice-list">
        <div class="notice"><a href="#">Lorem Ipsum is simply dummy text</a><p>Lorem Ipsum is simply dummy text of the printing and ting industry. <u>Date on 13 September 2016</u></p></div>
        <div class="notice"><a href="#">Lorem Ipsum is simply dummy text</a><p>Lorem Ipsum is simply dummy text of the printing and ting industry. <u>Date on 30 September 2016</u></p></div>
      </div>
    </div>
    <div class="newsletter">
      <h4>NEWSLETTER SIGNUP</h4>
      <form>
        <div class="field">- FIRST NAME -</div>
        <div class="field">- LAST NAME -</div>
        <div class="field">- E-MAIL -</div>
        <div class="btn">SIGN UP</div>
      </form>
    </div>
  </section>

  <footer class="site-footer">
    <div class="col c1">
      <h5>PICKUP LOCATIONS</h5>
      <ul><li>Harborline Marina - St. Petersburg</li><li>Pelican Point - Ruskin</li><li>Bayside Boat Ramp</li><li>Kingston Boat Ramp</li></ul>
    </div>
    <div class="col c2">
      <h5>CONTACT US</h5>
      <ul class="contact">
        <li><svg width="10" height="12" viewBox="0 0 10 12"><path d="M5 0a4 4 0 0 0-4 4c0 3 4 8 4 8s4-5 4-8a4 4 0 0 0-4-4z" fill="#bbb"/><circle cx="5" cy="4" r="1.5" fill="#1c1c1c"/></svg>reelcove Company name,</li>
        <li style="padding-left:18px">Street name,City-455</li>
        <li><svg width="10" height="10" viewBox="0 0 20 20"><path d="M4 1l4 .5 2 5-2.5 2a12 12 0 0 0 5 5l2-2.5 5 2 .5 4A2.5 2.5 0 0 1 17 19 16 16 0 0 1 1 3a2.5 2.5 0 0 1 3-2z" fill="#bbb"/></svg>Tel: 813-555-0182</li>
        <li><svg width="11" height="9" viewBox="0 0 11 9"><rect x=".5" y=".5" width="10" height="8" fill="none" stroke="#bbb"/><path d="M.5 .5l5 4 5-4" fill="none" stroke="#bbb"/></svg>Email: captwade@reelcovemail.net</li>
      </ul>
    </div>
    <div class="col c3">
      <h5>NEWS</h5>
      <span class="news-nav">‹ ›</span>
      <div class="news-item">
        <div class="news-photo" role="img" aria-label="Two anglers on a boat"></div>
        <p><b>Nam libero tempore, cum soluta</b><br>Lorem Ipsum is simply dummy text<br><em>Posted on 27August 2015</em></p>
      </div>
    </div>
    <div class="col c4">
      <h5>FOLLOW US</h5>
      <p>Culpa qui officia deserunt mollitia animi, id est...</p>
      <div class="social"><span></span><span></span><span></span><span></span></div>
    </div>
  </footer>
  <div class="copyright">© 2016 . CAPT. WADE HALVORSEN | ALLRIGHTS RESERVED.</div>

</div>
</body>
</html>
```